Plume Arc Website - Enabling Omni channel

Slogan : Enabling Omnichannel Sales

1. Sell products via multiple sale channels
2. Access our technology and services to get your products moving through new channels
3. Customise our mobile and web technology platforms to suit your supply chain.

Slogan: Plume arc – Innovating new business.

Use the content from these websites to create a new one
http://vorbankhq.com/
http://lorvane-designs.com/plumeArc02/

Target Market(s)

Business and Coporations who need mobile and web technology or services to increase product sales within their vertical industry. Our case studies show the industries we have worked in; namely: Retail, wholesale, online retail, motor and auto trade. Also have rich experience in Importing and Exporting.

Industry/Entity Type

Retail

Number of Pages Required

3 page

Font styles to use
Sans Serif

Colors
0255a3
ec1f27
9bcb3c
ffffff
0792cd
ffc214

Requirements
Must have
• Punchy headline home page with possible animations or unique and interesting images

```html
<!DOCTYPE html>
<html lang="en">
<head>
<meta charset="utf-8">
<title>Plume Arc – Innovating new business</title>
<link href="https://fonts.googleapis.com/css2?family=Open+Sans:wght@400;600;700&display=swap" rel="stylesheet">
<style>
:root{
  --brand-blue:#0255a3;
  --sky-blue:#0792cd;
  --heading-blue:#1b6fb5;
  --red:#ec1f27;
  --green:#9bcb3c;
  --yellow:#ffc214;
  --white:#ffffff;
  --ink:#222222;
  --body:#666666;
  --muted:#9a9a9a;
  --panel:#f2f2f2;
  --footer:#262626;
  --footer-base:#1c1c1c;
  --line:#d6d6d6;
}
*{box-sizing:border-box;margin:0;padding:0}
html,body{width:1200px;height:2317px;overflow:hidden}
body{font-family:"Open Sans",Arial,sans-serif;color:var(--ink);background:var(--white);position:relative}
.abs{position:absolute}
ul{list-style:none}

/* header */
.site-header{top:0;left:0;width:1200px;height:113px;background:var(--white)}
.brand{left:133px;top:34px;display:flex;align-items:center;gap:10px}
.brand-mark{width:14px;height:14px;border-radius:50%;background:var(--brand-blue)}
.brand-name{font-size:30px;font-weight:700;color:var(--brand-blue);line-height:1}
.brand-tag{left:243px;top:78px;font-size:11px;color:var(--ink)}
.main-nav{top:45px;font-size:12px;color:var(--ink)}
.main-nav.active{color:var(--brand-blue)}

/* hero */
.hero{top:113px;left:0;width:1200px;height:500px;background:linear-gradient(90deg,#5d5248 0%,#8a7a68 30%,#c5b7a3 55%,#b98f5f 80%,#d9b07a 100%)}
.hero-title{right:135px;top:330px;text-align:right;font-size:28px;font-weight:700;line-height:1.3;color:var(--white);text-shadow:0 1px 3px rgba(0,0,0,.4)}
.hero-dots{left:560px;top:580px;display:flex;gap:14px}
.hero-dots span{width:9px;height:9px;border-radius:50%;background:var(--white)}
.hero-dots span.current{background:transparent;border:2px solid var(--white)}

/* features */
.feature{width:300px;text-align:center;top:655px}
.feature-icon{width:76px;height:76px;border-radius:50%;border:1px solid var(--brand-blue);margin:0 auto;display:flex;align-items:center;justify-content:center}
.feature-title{margin-top:28px;font-size:21px;font-weight:600;color:var(--brand-blue)}
.feature-text{margin-top:10px;font-size:10.5px;line-height:16px;color:var(--body)}

/* bundle */
.bundle{top:883px;left:0;width:1200px;height:346px;background:var(--panel)}
.bundle-title{left:134px;top:922px;font-size:36px;font-weight:700;line-height:42px;color:var(--red);letter-spacing:.5px}
.bundle-sub{left:134px;top:1012px;font-size:12.5px;color:var(--ink)}
.gift{left:134px;top:1045px;width:141px;height:139px;border-radius:10px;background:linear-gradient(135deg,#e8534f,#c9302c)}
.offer-head{left:609px;font-size:16px;font-weight:600;color:var(--red);line-height:22px;width:460px}
.offer-icon{left:563px}
.offer-text{left:563px;top:968px;width:500px;font-size:10.5px;line-height:16px;color:var(--body)}
.offer-rule{left:563px;top:1043px;width:503px;height:1px;background:var(--line)}
.offer-list{left:563px;top:1120px;font-size:10.5px;line-height:15px;color:var(--body)}
.offer-list li::before{content:"•";margin-right:7px}

/* solutions */
.solutions-head{left:134px;top:1299px;width:420px;font-size:12.5px;line-height:17px;color:var(--ink)}
.solution-item{left:134px;font-size:12.5px;color:#555;display:flex;align-items:center;gap:9px;text-transform:uppercase}
.toggle{width:12px;height:12px;border-radius:50%;background:#444;color:var(--white);font-size:11px;line-height:12px;text-align:center;font-weight:700}
.solution-body{left:153px;top:1368px;width:448px;font-size:9.5px;line-height:14.5px;color:#aaa;text-align:justify}
.megaphone{left:664px;top:1297px;width:186px;height:186px;border-radius:50%;background:radial-gradient(circle at 55% 50%,#e85a4a 0 30%,#2c4a6b 31% 42%,#c5e6e4 43%)}
.marketing-title{left:659px;top:1484px;font-size:36px;font-weight:700;color:var(--green);letter-spacing:.5px}
.marketing-sub{left:661px;top:1536px;font-size:12px;font-weight:600;color:var(--ink)}
.marketing-list{left:661px;top:1562px;font-size:10.5px;line-height:21px;color:var(--body)}

/* situations */
.situations{top:1695px;left:0;width:1200px;height:309px;background:var(--panel)}
.col-title{top:1740px;font-size:15px;color:var(--heading-blue);text-transform:uppercase}
.col-list{top:1775px;font-size:11px;line-height:22px;color:var(--muted)}
.col-list li::before{content:"•";margin-right:7px}
.col-text{left:750px;top:1775px;width:316px;font-size:11px;line-height:22px;color:var(--muted);text-align:justify}
.contact-btn{top:1922px;width:82px;height:37px;border:1px solid #bbb;background:var(--white);font-size:11px;color:var(--ink);display:flex;align-items:center;justify-content:center;box-shadow:0 1px 2px rgba(0,0,0,.15)}

/* newsletter */
.newsletter{top:2004px;left:0;width:1200px;height:63px;background:var(--sky-blue)}
.newsletter-title{left:181px;top:2018px;font-size:25px;font-weight:700;color:var(--white);display:flex;align-items:center;gap:8px}
.field{top:2019px;width:192px;height:34px;background:var(--white);font-size:11px;color:#999;padding:9px 16px}
.subscribe{left:933px;top:2019px;width:79px;height:34px;background:#1d1d1d;color:var(--white);font-size:12px;display:flex;align-items:center;justify-content:center}

/* footer */
.site-footer{top:2067px;left:0;width:1200px;height:184px;background:var(--footer)}
.foot-title{top:2096px;font-size:12.5px;color:var(--white)}
.foot-list{top:2124px;font-size:9.5px;line-height:21px;color:#b8b8b8}
.foot-list li::before{content:"•";margin-right:6px}
.foot-divider{top:2093px;width:1px;height:130px;background:#3c3c3c}
.social{top:2129px;width:26px;height:26px;border-radius:50%;background:var(--brand-blue)}
.copyright{top:2251px;left:0;width:1200px;height:66px;background:var(--footer-base);font-size:10.5px;color:#aaa;display:flex;align-items:center;justify-content:center}
</style>
</head>
<body>

<header class="abs site-header">
  <div class="abs brand"><span class="brand-mark"></span><span class="brand-name">Plume Arc</span></div>
  <div class="abs brand-tag">Innovating new business</div>
  <a class="abs main-nav active" style="left:652px">Home</a>
  <a class="abs main-nav" style="left:712px">About us</a>
  <a class="abs main-nav" style="left:788px">Why us?</a>
  <a class="abs main-nav" style="left:860px">Case Studies</a>
  <a class="abs main-nav" style="left:956px">FAQs</a>
  <a class="abs main-nav" style="left:1011px">Contact us</a>
</header>

<section class="abs hero" role="img" aria-label="Photo of colleagues in discussion in a bright office"></section>
<h1 class="abs hero-title">Suspendisse tempus<br>condimentum rutrum</h1>
<div class="abs hero-dots"><span class="current"></span><span></span><span></span><span></span></div>

<div class="abs feature" style="left:130px">
  <div class="feature-icon"><svg width="30" height="22" viewBox="0 0 30 22"><rect x="5" y="2" width="20" height="14" rx="1.5" fill="none" stroke="#0255a3" stroke-width="2"/><path d="M1 18h28l-2 3H3z" fill="#0255a3"/></svg></div>
  <h3 class="feature-title">Updated Technology</h3>
  <p class="feature-text">Sed consequat diam eu mauris ultricies, nec tincidunt nulla porttitor. Ut convallis, vel laoreet condimentum, ante felis mollis lectus, eu venenatis ligula sapien.</p>
</div>
<div class="abs feature" style="left:452px">
  <div class="feature-icon"><svg width="34" height="32" viewBox="0 0 34 32"><circle cx="13" cy="18" r="7" fill="none" stroke="#0255a3" stroke-width="5" stroke-dasharray="3 2.5"/><circle cx="13" cy="18" r="3" fill="#0255a3"/><circle cx="25" cy="8" r="4.5" fill="none" stroke="#0255a3" stroke-width="3.5" stroke-dasharray="2 2"/><circle cx="26" cy="25" r="3.5" fill="none" stroke="#0255a3" stroke-width="3" stroke-dasharray="2 1.6"/></svg></div>
  <h3 class="feature-title">End-to-End Automation</h3>
  <p class="feature-text">Sed consequat diam eu mauris ultricies, nec tincidunt nulla porttitor. Ut convallis, vel laoreet condimentum, ante felis mollis lectus, eu venenatis ligula sapien.</p>
</div>
<div class="abs feature" style="left:773px">
  <div class="feature-icon"><svg width="28" height="27" viewBox="0 0 24 23"><path d="M12 1l3.2 7 7.6.7-5.8 5 1.8 7.5L12 17.3 5.2 21.2 7 13.7 1.2 8.7 8.8 8z" fill="#0255a3"/></svg></div>
  <h3 class="feature-title">Features</h3>
  <p class="feature-text">Sed consequat diam eu mauris ultricies, nec tincidunt nulla porttitor. Ut convallis, vel laoreet condimentum, ante felis mollis lectus, eu venenatis ligula sapien.</p>
</div>

<section class="abs bundle"></section>
<h2 class="abs bundle-title">AWESOME SERVICE<br>BUNDLE</h2>
<p class="abs bundle-sub">Plume Arc specializes in Feature-rich Services.</p>
<div class="abs gift" role="img" aria-label="Illustration of a red gift box with a white ribbon"></div>

<svg class="abs offer-icon" style="top:926px" width="24" height="24" viewBox="0 0 24 24"><path d="M6 2h12v6a6 6 0 0 1-12 0z" fill="#ec1f27"/><path d="M6 4H2v2a4 4 0 0 0 4 4M18 4h4v2a4 4 0 0 1-4 4" fill="none" stroke="#ec1f27" stroke-width="2"/><rect x="10.5" y="13" width="3" height="5" fill="#ec1f27"/><rect x="7" y="18" width="10" height="3" fill="#ec1f27"/></svg>
<h3 class="abs offer-head" style="top:925px">PARTNER WITH US TO DEVELOP A CUSTOM APP</h3>
<p class="abs offer-text">Whether you have an app in mind that needs developing or a business process requiring special attention our 20 plus years experience in start-ups, media and retailing means we're the right people to help you bring it to life.</p>
<div class="abs offer-rule"></div>
<svg class="abs offer-icon" style="top:1076px" width="26" height="26" viewBox="0 0 24 24"><path d="M21 3c-6 0-10 3-12.5 8l4.5 4.5C18 13 21 9 21 3z" fill="#ec1f27"/><path d="M8 10l-4 1-2 4 5-1zM14 16l-1 4-4 2 1-5z" fill="#ec1f27"/><path d="M6 16c-2 1-3 4-3 5 1 0 4-1 5-3" fill="#ec1f27"/></svg>
<h3 class="abs offer-head" style="top:1070px">INCORPORATE THE LATEST HARDWARE DEVICES AND TAGS TO BOOST BUSINESS</h3>
<ul class="abs offer-list">
  <li>Beacon tags – enhance customer's in-store experience (Orchard)</li>
  <li>NFC tags – enhance customer's in-store experience (Nimbus)</li>
  <li>RFid tags- track global supply chains</li>
  <li>Video and movement sensors – for in-store retail insights</li>
</ul>

<h3 class="abs solutions-head">LET US TAKE CARE OF THE SELLING WITH ONE OF OUR READY TO GO SOLUTIONS:SPECS</h3>
<div class="abs solution-item" style="top:1342px"><span class="toggle">–</span>Commissioned selling</div>
<p class="abs solution-body">We sell your products on commission. We find the channels to market. We find tradition retailers, online, and other outlets. Both locally and internationally. Many wholesalers enjoy using our websites as an additional channel, to avoid upsetting existing channels. Option for end-to-end sales solutions, you just bring the product. We'll use our in house software and expertise to drive your sales across multiple platforms like in-store, online and mobile and via job lots to distributors and retailers world-wide. Sales are commission based so we only earn when you earn.</p>
<div class="abs solution-item" style="top:1494px"><span class="toggle">+</span>Multi-channel selling</div>
<div class="abs solution-item" style="top:1522px"><span class="toggle">+</span>Managed or DIY web and Bazaar stores</div>
<div class="abs solution-item" style="top:1550px"><span class="toggle">+</span>Managed web and Bazaar stores</div>
<div class="abs solution-item" style="top:1577px"><span class="toggle">+</span>Export and retail management</div>
<div class="abs solution-item" style="top:1604px"><span class="toggle">+</span>Flash sales clearance and job lots</div>

<div class="abs megaphone" role="img" aria-label="Illustration of a red megaphone on a pale teal circle"></div>
<h2 class="abs marketing-title">MARKETING AND SALES</h2>
<p class="abs marketing-sub">WE GO TO THE ENDS OF THE EARTH TO GET YOUR PRODUCTS SELLING</p>
<ul class="abs marketing-list">
  <li>Broaden Customer reach with multi-channel Marketing.</li>
  <li>Be where Customers are by Selling Online and on Mobile.</li>
  <li>Be top of your Customer's mind using Loyalty.</li>
</ul>

<section class="abs situations"></section>
<h3 class="abs col-title" style="left:134px">Are you experiencing</h3>
<ul class="abs col-list" style="left:134px">
  <li>A website that hasn't brought in enough sales</li>
  <li>Need for a warehousing system to keep handling costs down</li>
  <li>Need for a retail website – separate to your existing website</li>
  <li>Need more retail products drop-shipped from more suppliers</li>
  <li>Requirement for distribution in your country or other countries</li>
</ul>
<h3 class="abs col-title" style="left:511px">Our solutions include</h3>
<ul class="abs col-list" style="left:511px">
  <li>Customer service</li>
  <li>Business Intelligence</li>
  <li>Advice and consulting</li>
  <li>Warehouse services</li>
  <li>Freight services</li>
  <li>Outsourced online retailing</li>
</ul>
<h3 class="abs col-title" style="left:750px">What to do now</h3>
<p class="abs col-text">If any of these situations are what you need, you're not alone. Many suppliers and manufacturers face these challenges. Plume Arc can help you create a marketing and sales plan for your situation, often incorporating our existing in-store and factory direct model using the Korvel supply chain.</p>
<a class="abs contact-btn" style="left:135px">Contact Us</a>
<a class="abs contact-btn" style="left:512px">Contact Us</a>
<a class="abs contact-btn" style="left:751px">Contact Us</a>

<section class="abs newsletter"></section>
<div class="abs newsletter-title"><svg width="24" height="18" viewBox="0 0 24 18"><rect x="1.5" y="1.5" width="21" height="15" rx="1.5" fill="none" stroke="#fff" stroke-width="2.2"/><path d="M2 3l10 7 10-7" fill="none" stroke="#fff" stroke-width="2.2"/></svg>NEWSLETTER SUBSCRIBE</div>
<div class="abs field" style="left:531px">Name</div>
<div class="abs field" style="left:732px">Email</div>
<div class="abs subscribe">Subscribe</div>

<footer class="abs site-footer"></footer>
<h4 class="abs foot-title" style="left:133px">Navigation Links</h4>
<ul class="abs foot-list" style="left:133px"><li>Home</li><li>About us</li><li>Why us?</li><li>Case Studies</li></ul>
<ul class="abs foot-list" style="left:254px"><li>FAQs</li><li>Contact us</li></ul>
<div class="abs foot-divider" style="left:367px"></div>
<h4 class="abs foot-title" style="left:417px">Services</h4>
<ul class="abs foot-list" style="left:417px"><li>Privacy Policy</li><li>Terms and Conditions</li><li>Sitemap</li></ul>
<div class="abs foot-divider" style="left:618px"></div>
<h4 class="abs foot-title" style="left:652px">Contact us</h4>
<ul class="abs foot-list" style="left:652px"><li>12 Fenwick Row, 4C Halden, Marlow City, USA</li><li>Phone : +61 2 5550 1742</li><li>Email : hello@plumearc.example</li></ul>
<div class="abs foot-divider" style="left:926px"></div>
<h4 class="abs foot-title" style="left:996px">Share us on</h4>
<span class="abs social" style="left:997px"></span>
<span class="abs social" style="left:1030px"></span>
<div class="abs copyright">Copyright ©&nbsp; 2016&nbsp; Plume Arc.&nbsp;&nbsp; All rights reserved.</div>

</body>
</html>
```